E learning Platform for privacy

Current website is as below and its more of a shell.
I need someone to take the text and content and design it properly.
https://study.vornaquill.com/

After that, design has to be implemented with elementor and wordpress
https://elementor.com/

```html
<!DOCTYPE html>
<html lang="en">
<head>
<meta charset="utf-8">
<title>Vornaquill Learning Centre</title>
<link href="https://fonts.googleapis.com/css2?family=Poppins:wght@300;400;500;600&display=swap" rel="stylesheet">
<style>
:root{
  --orange:#f7941d;
  --orange-deep:#e8572a;
  --ink:#333333;
  --muted:#555555;
  --dark:#333436;
  --bar:#565656;
  --soft:#f5f5f5;
  --white:#ffffff;
}
*{box-sizing:border-box;margin:0;padding:0}
html,body{width:1200px;height:3911px;overflow:hidden;background:var(--white)}
body{font-family:'Poppins',sans-serif;color:var(--ink);position:relative}
.abs{position:absolute}
.brand{font-weight:600;letter-spacing:2px;line-height:1}

/* header */
.site-header{left:0;top:0;width:1200px;height:103px;background:var(--white)}
.site-header .brand{left:111px;top:34px;font-size:30px;color:var(--orange)}
.main-nav{left:450px;top:40px;display:flex;font-size:15px;font-weight:500}
.main-nav span{padding:5px 9px;border-radius:16px}
.main-nav .active{background:var(--orange);color:var(--white)}
.btn{display:inline-flex;align-items:center;justify-content:center;background:var(--orange);color:var(--white);border-radius:30px;font-weight:500}
.register{left:972px;top:29px;width:116px;height:44px;font-size:16px}

/* hero */
.hero-photo{left:0;top:103px;width:1200px;height:620px;background:linear-gradient(100deg,#4a4139 0%,#6c5e52 35%,#a69786 60%,#7b6b5d 100%)}
.hero-curve{left:0;top:560px}
.hero .brand{left:111px;top:192px;font-size:58px;color:var(--white);letter-spacing:4px}
.hero h1{left:111px;top:300px;font-size:32px;font-weight:500;color:var(--white)}
.hero p{left:111px;top:350px;width:440px;font-size:19px;line-height:32px;color:var(--white)}
.get-trained{left:111px;top:437px;width:147px;height:58px;font-size:19px}

/* course cards */
.course-card{width:310px;height:491px;background:var(--white);box-shadow:0 3px 12px rgba(0,0,0,.18);text-align:center}
.course-card .thumb{position:absolute;left:12px;top:12px;width:286px;height:214px;background:linear-gradient(135deg,#c7ccd3,#7f8896 60%,#4b5360)}
.course-card h3{position:absolute;left:20px;right:20px;top:240px;font-size:21px;font-weight:500;line-height:26px;color:#3a3a3a}
.course-card .meta{position:absolute;left:0;right:0;top:312px;font-size:13px;color:var(--orange-deep)}
.course-card .meta span{margin:0 8px}
.course-card .desc{position:absolute;left:20px;right:20px;top:344px;font-size:14px;line-height:22px;color:var(--muted);font-weight:300}
.course-card .duration{position:absolute;left:0;bottom:0;width:100%;height:62px;background:var(--bar);color:var(--white);font-size:19px;font-weight:500;display:flex;align-items:center;justify-content:center}
.course-card.featured .duration{background:var(--orange)}

/* stats */
.stat{width:194px;height:194px;border-radius:50%;border:3px dashed var(--white);display:flex;align-items:center;justify-content:center}
.stat .disc{width:166px;height:166px;border-radius:50%;background:var(--orange);color:var(--white);display:flex;flex-direction:column;align-items:center;justify-content:center;text-align:center}
.stat.deep .disc{background:var(--orange-deep)}
.stat b{font-size:46px;font-weight:500;line-height:1}
.stat small{font-size:16px;font-weight:500;line-height:22px;margin-top:6px}

/* section heads */
.section-title{left:0;width:1200px;text-align:center;font-size:31px;font-weight:500;color:var(--orange)}
.section-lead{left:140px;width:920px;text-align:center;font-size:15px;line-height:25px;color:var(--muted);font-weight:300}

/* features */
.feature{width:300px}
.feature h4{font-size:22px;font-weight:500;line-height:26px;color:var(--orange);white-space:nowrap}
.feature h4.dark{color:#333}
.feature p{font-size:14px;line-height:21px;color:var(--muted);font-weight:300;text-align:justify;margin-top:4px}
.feature.left{text-align:right}
.feature.left p{text-align-last:right}
.icon-disc{width:66px;height:66px;border-radius:50%;background:var(--orange);display:flex;align-items:center;justify-content:center}
.icon-disc.dark{background:#3a3a3a}
.phone{left:500px;top:1815px;width:203px;height:413px;border:7px solid #111;border-radius:30px;background:var(--white);text-align:center}
.phone .notch{position:absolute;left:50px;top:0;width:90px;height:18px;background:#111;border-radius:0 0 14px 14px}
.phone .brand{position:absolute;left:0;right:0;top:118px;font-size:24px;color:var(--orange)}
.phone .tag{position:absolute;left:0;right:0;top:190px;font-size:19px;font-weight:500;line-height:29px}
.phone .btn{position:absolute;left:26px;top:307px;width:137px;height:46px;font-size:16px}

/* blog */
.blog-band{left:0;top:2289px}
.blog h2{left:656px;top:2398px;font-size:31px;font-weight:500;color:var(--orange)}
.blog .lead{left:656px;top:2455px;width:433px;font-size:15px;line-height:25px;color:var(--muted);font-weight:300}
.date-box{left:656px;top:2547px;width:79px;height:129px;background:var(--orange);color:var(--white);text-align:center;font-size:25px;font-weight:500;line-height:34px;padding-top:10px}
.post-title{left:752px;top:2540px;font-size:30px;font-weight:500;color:#333}
.post-text{left:752px;top:2585px;width:336px;font-size:15px;line-height:25px;color:var(--muted);font-weight:300;text-align:justify}
.read-more{left:752px;top:2734px;width:118px;height:44px;font-size:16px}

/* testimonials */
.quote-card{width:465px;height:298px;background:var(--white);box-shadow:0 3px 12px rgba(0,0,0,.13);overflow:hidden;border-radius:0 0 50% 50% / 0 0 14% 14%}
.quote-card p{position:absolute;left:18px;right:18px;top:30px;font-size:15px;line-height:27px;color:var(--muted);font-weight:300;text-align:justify}
.quote-card .who{position:absolute;top:190px;font-size:17px}
.quote-mark{position:absolute;width:140px;height:140px;border-radius:50%;color:var(--white);font-size:110px;font-weight:600;line-height:150px;text-align:center}

/* footer */
.footer .brand{left:111px;top:3582px;font-size:40px;color:var(--white);letter-spacing:3px}
.footer .name{left:111px;top:3676px;font-size:19px;font-weight:500;color:var(--white)}
.badge{left:111px;top:3723px;width:98px;height:32px;background:#e8e8e8;border:2px solid #8aa}
.foot-col h5{font-size:20px;font-weight:500;color:var(--white);margin-bottom:12px}
.foot-col li{list-style:none;font-size:16px;color:var(--white);line-height:30px;display:flex;align-items:center;gap:12px}
.foot-col .dot{width:5px;height:5px;background:var(--white);border-radius:50%}
.foot-col .ring{width:14px;height:14px;border:2px solid var(--white);border-radius:50%;margin-right:8px}
.copyright{left:111px;top:3858px;font-size:16px;color:var(--white)}
.powered{left:796px;top:3850px;font-size:16px;color:var(--white);display:flex;gap:26px;align-items:center}
.powered b{font-size:22px;font-weight:600}
</style>
</head>
<body>

<header class="site-header abs">
  <div class="brand abs">VORNAQUILL</div>
  <nav class="main-nav abs">
    <span class="active">HOME</span><span>BLOGS</span><span>COURSES</span><span>CONTACT US</span><span>ABOUT US</span><span>SIGN IN</span>
  </nav>
  <div class="btn register abs">REGISTER</div>
</header>

<section class="hero">
  <div class="hero-photo abs" role="img" aria-label="Woman reading thoughtfully on a sofa with a mug"></div>
  <svg class="hero-curve abs" width="1200" height="170" viewBox="0 0 1200 170"><path d="M0 110 Q600 -20 1200 110 V170 H0Z" fill="#fff"/></svg>
  <div class="brand abs">VORNAQUILL</div>
  <h1 class="abs">PRIVACY PRACTICE MASTERY</h1>
  <p class="abs">Largest online e-learning resource for data protection &amp; privacy</p>
  <div class="btn get-trained abs">GET TRAINED</div>
</section>

<section class="courses">
  <article class="course-card abs" style="left:111px;top:598px">
    <div class="thumb" role="img" aria-label="Instructor teaching a computer class"></div>
    <h3>How to Scale Social Impact</h3>
    <div class="meta"><span>▢ Dec 19, 2019</span><span>◯ Mr. Example</span></div>
    <p class="desc">Our objective is to provide a comprehensive competency roadmap, instead of one-off courses.</p>
    <div class="duration">Duration 55 Weeks</div>
  </article>
  <article class="course-card featured abs" style="left:445px;top:633px">
    <div class="thumb" role="img" aria-label="Students working at computers in a lab"></div>
    <h3>Lernex Demonstration Course</h3>
    <div class="meta"><span>▢ Dec 19, 2019</span><span>◯ Mr. Example</span></div>
    <p class="desc">Our objective is to provide a comprehensive competency roadmap, instead of one-off courses.</p>
    <div class="duration">Duration 55 Weeks</div>
  </article>
  <article class="course-card abs" style="left:779px;top:598px">
    <div class="thumb" role="img" aria-label="Students in a bright computer room"></div>
    <h3>How to Get Job Opportunities</h3>
    <div class="meta"><span>▢ Dec 19, 2019</span><span>◯ Mr. Example</span></div>
    <p class="desc">Our objective is to provide a comprehensive competency roadmap, instead of one-off courses.</p>
    <div class="duration">Duration 55 Weeks</div>
  </article>
</section>

<section class="stats">
  <svg class="abs" style="left:0;top:1180px" width="1200" height="432" viewBox="0 0 1200 432" role="img" aria-label="Dark keyboard with a globe and study items">
    <defs><linearGradient id="statsTone" x1="0" y1="0" x2="1" y2="1"><stop offset="0" stop-color="#1e2733"/><stop offset=".5" stop-color="#2f3a46"/><stop offset="1" stop-color="#1a2029"/></linearGradient></defs>
    <path d="M0 90 Q600 0 1200 2 V432 Q600 300 0 380Z" fill="url(#statsTone)"/>
  </svg>
  <div class="stat abs" style="left:148px;top:1297px"><div class="disc"><b>6,375</b><small>ENROLLED<br>STUDENTS</small></div></div>
  <div class="stat deep abs" style="left:506px;top:1293px"><div class="disc"><b>114</b><small>LESSONS</small></div></div>
  <div class="stat abs" style="left:863px;top:1297px"><div class="disc"><b>169</b><small>VIDEOS</small></div></div>
</section>

<section class="why">
  <h2 class="section-title abs" style="top:1655px">Why The (Vornaquill) Learning Centre?</h2>
  <p class="section-lead abs" style="top:1717px">Our mission at the Privacy Practice Mastery (Vornaquill) Learning Centre is to provide business and job opportunities, as well as to enhance personal and career advancement for data protection / privacy professionals.</p>

  <div class="feature left abs" style="left:105px;top:1848px"><h4>Comprehensive Roadmap</h4><p>Our objective is to provide a comprehensive competency roadmap, instead of one-off courses</p></div>
  <div class="feature left abs" style="left:105px;top:1967px"><h4 class="dark">Academic &amp;<br>International Certification</h4><p>We partner with prominent universities in the region as well as international certification bodies</p></div>
  <div class="feature left abs" style="left:105px;top:2105px"><h4>Network with other peers</h4><p>Participate in our online communities and discussion rooms and your network with other like-minded course</p></div>

  <div class="icon-disc abs" style="left:415px;top:1858px"><svg width="34" height="34" viewBox="0 0 34 34"><circle cx="17" cy="17" r="14" fill="none" stroke="#fff" stroke-width="3"/><path d="M23 11 L19 19 L11 23 L15 15Z" fill="#fff"/></svg></div>
  <div class="icon-disc dark abs" style="left:415px;top:1977px"><svg width="34" height="34" viewBox="0 0 34 34"><path d="M9 5 H25 V12 Q25 20 17 21 Q9 20 9 12Z M15 21 H19 V26 H23 V30 H11 V26 H15Z" fill="#fff"/></svg></div>
  <div class="icon-disc abs" style="left:415px;top:2113px"><svg width="36" height="30" viewBox="0 0 36 30"><path d="M2 8 L10 6 L18 12 L26 6 L34 8 V20 L22 26 L14 20 L2 18Z" fill="#fff"/></svg></div>

  <div class="phone abs"><div class="notch"></div><div class="brand">VORNAQUILL</div><div class="tag">PRIVACY<br>PRACTICE<br>MASTERY</div><div class="btn">LEARN MORE</div></div>

  <div class="icon-disc abs" style="left:719px;top:1858px"><svg width="34" height="30" viewBox="0 0 34 30"><path d="M12 3 H22 V8 H31 V27 H3 V8 H12Z M15 6 V8 H19 V6Z" fill="#fff"/></svg></div>
  <div class="icon-disc dark abs" style="left:719px;top:1977px"><svg width="34" height="34" viewBox="0 0 34 34"><rect x="4" y="18" width="11" height="11" fill="#fff"/><rect x="19" y="18" width="11" height="11" fill="#fff"/><rect x="11" y="5" width="11" height="11" fill="#fff"/></svg></div>
  <div class="icon-disc abs" style="left:719px;top:2113px"><svg width="34" height="34" viewBox="0 0 34 34"><path d="M30 4 L4 15 L15 18 L18 30Z" fill="#fff"/></svg></div>

  <div class="feature abs" style="left:796px;top:1848px"><h4>Operational Perspective</h4><p>We cover a broad range of data protection topics from both a legal and operational perspective, covering.</p></div>
  <div class="feature abs" style="left:796px;top:1967px"><h4 class="dark">Modular Approach &amp;<br>Flexibility</h4><p>All our courses are modular in nature to cater to the busy professional, meaning that you can take the courses.</p></div>
  <div class="feature abs" style="left:796px;top:2105px"><h4>Business and Job<br>Opportunities</h4><p>Collaborate with other professionals on potential business opportunities whether it relates to consultancy.</p></div>
</section>

<section class="blog">
  <svg class="blog-band abs" width="1200" height="620" viewBox="0 0 1200 620">
    <defs><linearGradient id="blogTone" x1="0" y1="0" x2="1" y2="1"><stop offset="0" stop-color="#3c4a5c"/><stop offset=".5" stop-color="#8a8f96"/><stop offset="1" stop-color="#c9c4bd"/></linearGradient></defs>
    <path d="M0 0 Q700 70 1200 40 V620 H0Z" fill="#f5f5f5"/>
    <path d="M0 0 Q300 50 548 50 Q470 180 520 330 Q560 470 470 600 Q250 560 0 610Z" fill="url(#blogTone)" role="img" aria-label="Smiling woman working on a laptop"/>
    <path d="M0 610 Q600 540 1200 610 V620 H0Z" fill="#fff"/>
  </svg>
  <h2 class="abs">Blog</h2>
  <svg class="abs" style="left:1028px;top:2402px" width="60" height="36" viewBox="0 0 60 36"><path d="M18 4 L6 18 L18 32 M42 4 L54 18 L42 32" fill="none" stroke="#333" stroke-width="3"/></svg>
  <p class="lead abs">All our courses are modular in nature to cater to the busy professional, meaning that you can take the courses</p>
  <div class="date-box abs">JAN<br>12<br>2020</div>
  <h3 class="post-title abs">Duis aute irure dolor</h3>
  <p class="post-text abs">Nemo enim ipsam voluptatem quia voluptas sit aspernatur aut odit aut fugit, sed quia consequuntur magni dolores eos qui ratione voluptatem sequi nesciunt. Neque porro quisquam est.</p>
  <div class="btn read-more abs">READ MORE</div>
</section>

<section class="testimonials">
  <h2 class="section-title abs" style="top:2933px">What People Say</h2>
  <p class="section-lead abs" style="top:2994px">Our mission at the Privacy Practice Mastery (Vornaquill) Learning Centre is to provide business and job opportunities, as well as to enhance personal and career advancement for data protection / privacy professionals.</p>
  <svg class="abs" style="left:32px;top:3198px" width="30" height="46" viewBox="0 0 30 46"><path d="M24 3 L6 23 L24 43" fill="none" stroke="#555" stroke-width="3"/></svg>
  <svg class="abs" style="left:1130px;top:3198px" width="30" height="46" viewBox="0 0 30 46"><path d="M6 3 L24 23 L6 43" fill="none" stroke="#555" stroke-width="3"/></svg>
  <article class="quote-card abs" style="left:111px;top:3089px">
    <p>Nemo enim ipsam voluptatem quia voluptas sit aspernatur aut odit aut fugit, sed quia consequuntur magni dolores eos qui ratione voluptatem sequi nesciunt. Neque porro quisquam est, qui dolorem ipsum quia dolor sit amet, consectetur, adipisci velit.</p>
    <div class="who" style="left:18px;color:var(--orange)">-John Smith</div>
    <div class="quote-mark" style="left:335px;top:168px;background:var(--orange)">”</div>
  </article>
  <article class="quote-card abs" style="left:624px;top:3089px">
    <p style="text-align-last:right">Nemo enim ipsam voluptatem quia voluptas sit aspernatur aut odit aut fugit, sed quia consequuntur magni dolores eos qui ratione voluptatem sequi nesciunt. Neque porro quisquam est, qui dolorem ipsum quia dolor sit amet, consectetur, adipisci velit.</p>
    <div class="who" style="right:18px;color:#444">-Clara</div>
    <div class="quote-mark" style="left:-4px;top:180px;background:#3a3a3a">“</div>
  </article>
</section>

<footer class="footer">
  <svg class="abs" style="left:0;top:3388px" width="1200" height="523" viewBox="0 0 1200 523">
    <path d="M0 0 H1200 V523 H0Z" fill="#333436"/>
    <path d="M0 0 Q600 200 1200 0Z" fill="#fff"/>
    <path d="M0 430 Q600 360 1200 410 V523 H0Z" fill="#f7941d"/>
  </svg>
  <div class="brand abs">VORNAQUILL</div>
  <div class="name abs">VORNAQUILL LEARNING CENTRE</div>
  <div class="badge abs"></div>
  <div class="foot-col abs" style="left:460px;top:3588px"><h5>COMPANY</h5><ul><li><i class="dot"></i>About</li><li><i class="dot"></i>Courses</li><li><i class="dot"></i>FAQs</li></ul></div>
  <div class="foot-col abs" style="left:696px;top:3588px"><h5>GET INVOLVED</h5><ul><li><i class="dot"></i>Blog</li><li><i class="dot"></i>Contact</li></ul></div>
  <div class="foot-col abs" style="left:955px;top:3588px"><h5>CONNECT</h5><ul><li><i class="ring"></i>Friendwall</li><li><i class="ring"></i>Chirper</li><li><i class="ring"></i>Workline</li><li><i class="ring"></i>Snapgrid</li></ul></div>
  <div class="copyright abs">Copyrights @ 2020 Vornaquill Center. All Rights Reserved.</div>
  <div class="powered abs"><span>Powered by:</span><b>Kovly</b><span>OPENLERNEX</span></div>
</footer>

</body>
</html>
```